Chimney Service company needs new business card design

We need a updated business card with our new logo added. We provide a full range of chimney services throughout Vermont and New Hampshire. The business card will be one sided and color. Attached is our current business card another document showing all the information we would like on the card.
We dont like a lot of flashy colors.... here is a link to our website to get an idea of our branding www.flueguardianvt.example

Target Market(s)

homeowners

Industry/Entity Type

Business

Contact Information for Business Card

See attached sheet for content.

Font styles to use
Serif
Sans Serif

Requirements
Must have
• all information provided on separate sheet
Should not have
• Additional information that may clogg up design

```html
<!DOCTYPE html>
<html lang="en">
<head>
<meta charset="utf-8">
<title>Flue Guardian – Business Card</title>
<link href="https://fonts.googleapis.com/css2?family=Cinzel:wght@400;500&family=Didact+Gothic&display=swap" rel="stylesheet">
<style>
  :root {
    --backdrop: #e9e6e1;
    --card-top: #3a3b3d;
    --card-mid: #2d2e30;
    --card-bottom: #242527;
    --ink-light: #e8e8e8;
    --ink-soft: #c9c9c9;
    --accent-red: #b3242b;
    --rule-white: #d9d9d9;
  }
  * { margin: 0; padding: 0; box-sizing: border-box; }
  html, body {
    width: 1200px;
    height: 1022px;
    overflow: hidden;
    background: var(--backdrop);
  }
  .card {
    position: absolute;
    left: 150px;
    top: 254px;
    width: 900px;
    height: 514px;
    border-radius: 4px;
    background: linear-gradient(160deg, var(--card-top) 0%, var(--card-mid) 50%, var(--card-bottom) 100%);
    box-shadow: 0 14px 34px rgba(0,0,0,0.28);
    overflow: hidden;
  }
  .contact {
    position: absolute;
    right: 48px;
    top: 46px;
    text-align: right;
    font-family: "Didact Gothic", sans-serif;
    color: var(--ink-light);
    font-size: 25px;
    line-height: 36px;
    letter-spacing: 0.5px;
  }
  .contact-icons {
    position: absolute;
    right: 48px;
    top: 10px;
    display: flex;
    gap: 6px;
  }
  .contact-icons svg { width: 22px; height: 22px; }
  .contact-lines { margin-top: 2px; }
  .brand {
    position: absolute;
    left: 60px;
    top: 180px;
    width: 330px;
    text-align: center;
  }
  .brand-mark {
    width: 108px;
    height: 108px;
    border: 9px solid var(--ink-light);
    margin: 0 auto 22px;
  }
  .brand-name {
    font-family: "Cinzel", serif;
    font-weight: 400;
    font-size: 38px;
    color: var(--ink-light);
    letter-spacing: 1.5px;
    white-space: nowrap;
  }
  .brand-since {
    display: flex;
    align-items: center;
    gap: 10px;
    margin-top: 8px;
    font-family: "Cinzel", serif;
    font-size: 17px;
    color: var(--ink-soft);
    letter-spacing: 2px;
  }
  .brand-since::before, .brand-since::after {
    content: "";
    flex: 1;
    height: 2px;
    background: var(--ink-light);
  }
  .divider-red {
    position: absolute;
    left: 420px;
    top: 175px;
    width: 3px;
    height: 270px;
    background: var(--accent-red);
  }
  .services {
    position: absolute;
    left: 452px;
    top: 228px;
    list-style: none;
    font-family: "Cinzel", serif;
    font-size: 20px;
    text-transform: uppercase;
    color: var(--ink-light);
    line-height: 40px;
    letter-spacing: 0.6px;
    white-space: nowrap;
  }
  .services li::before {
    content: "";
    display: inline-block;
    width: 9px;
    height: 9px;
    border-radius: 50%;
    background: var(--ink-light);
    margin-right: 12px;
    vertical-align: middle;
    position: relative;
    top: -2px;
  }
  .rule-bottom {
    position: absolute;
    left: 40px;
    right: 40px;
    bottom: 26px;
    height: 3px;
    background: var(--rule-white);
  }
</style>
</head>
<body>
  <div class="card">
    <div class="contact-icons" aria-hidden="true">
      <svg viewBox="0 0 22 22"><circle cx="11" cy="11" r="11" fill="var(--accent-red)"/><path d="M7 6c1 0 2 2 2 3s-1 1-1 1c1 2 2 3 4 4 0 0 0-1 1-1s3 1 3 2-1 2-2 2c-4 0-8-4-8-8 0-1 0-3 1-3z" fill="#fff"/></svg>
      <svg viewBox="0 0 22 22"><circle cx="11" cy="11" r="11" fill="var(--accent-red)"/><g fill="none" stroke="#fff" stroke-width="1.3"><circle cx="11" cy="11" r="6"/><ellipse cx="11" cy="11" rx="2.5" ry="6"/><path d="M5 11h12M6 8h10M6 14h10"/></g></svg>
      <svg viewBox="0 0 22 22"><rect width="22" height="22" rx="3" fill="var(--accent-red)"/><g fill="none" stroke="#fff" stroke-width="1.3"><rect x="5" y="7" width="12" height="8"/><path d="M5 7l6 5 6-5"/></g></svg>
    </div>
    <div class="contact">
      <div class="contact-lines">
        <div>802-555-0147</div>
        <div>info@flueguardianvt.example</div>
        <div>www.flueguardianvt.example</div>
      </div>
    </div>

    <div class="brand">
      <div class="brand-mark"></div>
      <div class="brand-name">FLUE GUARDIAN</div>
      <div class="brand-since">INC 1994</div>
    </div>

    <div class="divider-red"></div>

    <ul class="services">
      <li>Full Masonry Services</li>
      <li>Historic Chimney Restoration</li>
      <li>Stainless Steel Liners</li>
      <li>Fully Certified Chimney Sweep</li>
      <li>Fully Insured • Free Estimates</li>
    </ul>

    <div class="rule-bottom"></div>
  </div>
</body>
</html>
```